Ward Compass Business Card Design*

We need a business card design for our company Ward Compass. Our company is specialized in providing online consulting services regarding medical institutions, hospitals and doctors. We work with patients worldwide looking to choose between healthcare providers. We have a website you may use as a reference, where we list doctors and clinics worldwide. So we target Medical providers as well as patients worldwide.
Target Market(s)
Medical Providers and patients around the world
Industry/Entity Type
Medical
Contact Information for Business Card
Salwa Kettani
CEO
+90 612 348 2175
info@wardcompass.example
www.wardcompass.example
14 Annakhil 7 H.R.B. Rabat, Morocco
Requirements
Must have
- Company logo/name on one full side, personal info and smaller logo and company name on the other side.
Nice to have
- Smart and elegant design

```html
<!DOCTYPE html>
<html lang="en">
<head>
<meta charset="utf-8">
<title>Ward Compass – Business Card</title>
<link href="https://fonts.googleapis.com/css2?family=Montserrat:wght@300;400;700&display=swap" rel="stylesheet">
<style>
  :root {
    --backdrop: #1c1d21;
    --navy: #1e3361;
    --navy-deep: #141d33;
    --grey: #7d7f84;
    --grey-text: #5a5c60;
    --paper: #ffffff;
  }
  * { box-sizing: border-box; margin: 0; padding: 0; }
  html, body {
    width: 1200px; height: 800px; overflow: hidden;
    background: var(--backdrop);
    font-family: "Montserrat", Arial, sans-serif;
  }
  .canvas {
    width: 1200px; height: 800px;
    display: flex; align-items: center; justify-content: center; gap: 40px;
  }
  .card {
    width: 540px; height: 309px; position: relative;
    box-shadow: 0 18px 40px rgba(0,0,0,.45);
  }
  .card--front {
    background: var(--navy);
    display: flex; align-items: center; justify-content: center; gap: 14px;
  }
  .brand { display: flex; align-items: center; gap: 12px; }
  .brand__dot { width: 42px; height: 42px; border-radius: 50%; flex: none; }
  .brand__name {
    font-weight: 400; letter-spacing: 2px; text-transform: uppercase; white-space: nowrap;
  }
  .card--front .brand__dot { background: var(--navy-deep); width: 58px; height: 58px; }
  .card--front .brand__name { color: var(--navy-deep); font-size: 27px; }

  .card--back { background: var(--paper); }
  .card--back .brand {
    position: absolute; left: 34px; top: 50%; transform: translateY(-50%);
  }
  .card--back .brand__dot { background: var(--navy); }
  .card--back .brand__name { color: var(--grey); font-size: 19px; }
  .divider {
    position: absolute; left: 300px; top: 78px; width: 1.5px; height: 150px;
    background: var(--navy);
  }
  .contact { position: absolute; left: 322px; top: 86px; }
  .contact__name { font-size: 16px; color: var(--grey-text); font-weight: 400; letter-spacing: .5px; }
  .contact__name strong { color: var(--navy); font-weight: 700; }
  .contact__role { font-size: 12px; color: var(--grey-text); margin-top: 2px; }
  .contact__list { list-style: none; margin-top: 20px; }
  .contact__item {
    display: flex; align-items: center; gap: 8px;
    font-size: 10.5px; color: var(--grey-text); margin-bottom: 8px;
  }
  .contact__icon {
    width: 16px; height: 16px; border-radius: 50%; background: var(--navy);
    display: flex; align-items: center; justify-content: center; flex: none;
  }
</style>
</head>
<body>
<main class="canvas">
  <section class="card card--front" aria-label="Card front">
    <div class="brand">
      <span class="brand__dot"></span>
      <span class="brand__name">Ward Compass</span>
    </div>
  </section>

  <section class="card card--back" aria-label="Card back">
    <div class="brand">
      <span class="brand__dot"></span>
      <span class="brand__name">Ward Compass</span>
    </div>
    <div class="divider"></div>
    <div class="contact">
      <p class="contact__name"><strong>SALWA</strong> KETTANI</p>
      <p class="contact__role">CEO</p>
      <ul class="contact__list">
        <li class="contact__item">
          <span class="contact__icon">
            <svg width="9" height="9" viewBox="0 0 24 24"><path fill="#fff" d="M6.6 10.8a15 15 0 0 0 6.6 6.6l2.2-2.2a1 1 0 0 1 1-.25 11.4 11.4 0 0 0 3.6.57 1 1 0 0 1 1 1V20a1 1 0 0 1-1 1A17 17 0 0 1 3 4a1 1 0 0 1 1-1h3.5a1 1 0 0 1 1 1c0 1.25.2 2.45.57 3.57a1 1 0 0 1-.25 1z"/></svg>
          </span>
          +90 612 348 2175
        </li>
        <li class="contact__item">
          <span class="contact__icon">
            <svg width="9" height="9" viewBox="0 0 24 24"><path fill="#fff" d="M3 5h18v14H3z"/><path fill="none" stroke="#1e3361" stroke-width="2" d="M3 6l9 7 9-7"/></svg>
          </span>
          info@wardcompass.example
        </li>
        <li class="contact__item">
          <span class="contact__icon">
            <svg width="10" height="10" viewBox="0 0 24 24" fill="none" stroke="#fff" stroke-width="2"><circle cx="12" cy="12" r="9"/><path d="M3 12h18M12 3c3 3 3 15 0 18M12 3c-3 3-3 15 0 18"/></svg>
          </span>
          www.wardcompass.example
        </li>
      </ul>
    </div>
  </section>
</main>
</body>
</html>
```